Digital Marketing Agency Landing Page

At VELIM, we offer a comprehensive solution for solar companies' client acquisition needs in the rapidly growing industry. We handle end-to-end client acquisition, meaning we manage the entire lifecycle of capturing new clients—from initial lead generation to delivering the ready-to-buy homeowner. Our expertise in targeted advertising, data analytics, and customer relationship management ensures that we not only find potential customers but also nurture them through tailored engagement strategies until they are ready to make a purchase. By entrusting us with your client acquisition process, solar companies can focus on what they do best—providing sustainable energy solutions—while we work behind the scenes to grow your customer base and increase your market share.

We need to restructure our website to make it more professional. We don't need any complex functionalities. We are looking for someone that is good in design and can build a visually aesthetic website following our brand image. We only need a landing page and a lead form in the end. I would like to have only one page, but a relatively big one where people scroll down. I would like to have a minimal and classy look. Something that is timeless and elegant.

Structure:

initial page
About us
How we operate
Get in touch

Target Market(s)

Solar Comapanies

Industry/Entity Type

Marketing solautions

Coding

Coded - Design and coding required

Number of Pages Required

1 page

Requirements
Nice to have
• Inspirations: https://www.qz.zu/ https://www.marchbeck.example/ https://www.tovanrid.example/ https://pruvo.example/

```html
<!DOCTYPE html>
<html lang="en">
<head>
<meta charset="utf-8">
<title>VELIM — Digital Marketing for Solar Companies</title>
<link rel="stylesheet" href="https://fonts.googleapis.com/css2?family=Montserrat:wght@300;400;500;600;700&display=swap">
<style>
:root{
  --header:#14222e;
  --navy:#1b3040;
  --navy-deep:#152634;
  --charcoal:#272727;
  --black:#050505;
  --cream:#ece6d9;
  --white:#ffffff;
  --line:#e8e4dc;
}
*{box-sizing:border-box;margin:0;padding:0}
html,body{width:1200px;height:3452px;overflow:hidden;background:var(--black)}
body{font-family:"Montserrat",sans-serif;color:var(--white)}
.page{position:relative;width:1200px;height:3452px;overflow:hidden}
.abs{position:absolute}

/* header */
.site-header{left:0;top:0;width:1200px;height:127px;background:var(--header);z-index:3}
.brand{left:114px;top:21px;width:207px;height:79px;display:flex;align-items:center;justify-content:center;
  font-weight:300;font-size:44px;letter-spacing:1px;color:var(--cream)}
.icon-search{left:980px;top:46px}
.icon-menu{left:1052px;top:46px}

/* backgrounds */
.bg-navy{left:0;top:127px;width:1200px;height:1340px;background:radial-gradient(ellipse at 55% 40%,#213a4c 0%,var(--navy) 55%,var(--navy-deep) 100%)}
.bg-services{left:0;top:1430px;width:1200px;height:900px;background:var(--charcoal)}
.bg-contact{left:0;top:2200px;width:1200px;height:900px;
  background:
   repeating-linear-gradient(90deg,rgba(120,160,190,.07) 0 2px,transparent 2px 64px),
   repeating-linear-gradient(0deg,rgba(120,160,190,.07) 0 2px,transparent 2px 64px),
   linear-gradient(180deg,#1a2f3f 0%,#1c3344 50%,#162a38 100%)}
.bg-footer{left:0;top:2980px;width:1200px;height:472px;background:var(--black)}
.divider{left:0;width:1200px}

/* hero */
.hero-visual{left:0;top:127px;width:1200px;height:670px;
  background:radial-gradient(ellipse at 72% 45%,#2e86c4 0%,#1a5b8e 22%,#103a5c 45%,#0b2236 75%),#0b2236;
  clip-path:polygon(0 0,100% 0,100% 603px,847px 540px,0 656px)}
.hero-kicker{left:114px;top:250px;font-size:45px;font-weight:400;letter-spacing:1px;color:var(--cream)}
.hero-title{left:110px;top:318px;font-size:124px;font-weight:400;letter-spacing:2px;line-height:1;color:var(--cream)}

.btn-frame{position:absolute;display:flex;align-items:center;justify-content:center;
  border:2px solid var(--line);color:var(--cream);font-weight:400;letter-spacing:.5px}
.btn-frame::after{content:"";position:absolute;left:8px;top:8px;right:-8px;bottom:-8px;border:2px solid var(--line)}
.hero-cta{left:114px;top:478px;width:162px;height:61px;font-size:19px}

/* about */
.frame{border:2px solid var(--line)}
.about-frame-a{left:127px;top:881px;width:914px;height:412px}
.about-frame-b{left:161px;top:923px;width:912px;height:410px}
.about-title{left:0;top:985px;width:1200px;text-align:center;font-size:45px;font-weight:700;letter-spacing:.5px}
.about-text{left:200px;top:1072px;width:800px;text-align:center;font-size:17.5px;line-height:30px;font-weight:400}

/* services */
.section-title{left:0;width:1200px;text-align:center;font-size:45px;font-weight:700;letter-spacing:.5px}
.services-title{top:1627px}
.service-card{top:1743px;width:303px;height:367px;border:2px solid var(--line)}
.service-card .thumb{position:absolute;left:23px;top:27px;width:253px;height:176px}
.service-card h3{position:absolute;left:10px;right:10px;top:220px;text-align:center;font-size:23px;font-weight:600;line-height:31px}
.service-card p{position:absolute;left:28px;right:28px;text-align:center;font-size:14.5px;line-height:21.5px}
.card-1{left:111px}.card-2{left:449px}.card-3{left:786px}
.thumb-ads{background:linear-gradient(135deg,#a9b7c2 0%,#6d7d8a 45%,#c8a88a 70%,#3d4a57 100%)}
.thumb-data{background:linear-gradient(135deg,#e9eaed 0%,#4a5561 40%,#24303c 60%,#d9dcdf 100%)}
.thumb-crm{background:radial-gradient(ellipse at 50% 50%,#69d2e6 0%,#1f8fac 45%,#0f5f78 100%)}

/* contact */
.contact-title{top:2378px}
.field{position:absolute;border:2px solid var(--line);font-size:15px;padding:22px 0 0 22px;color:var(--white)}
.f-name{left:184px;top:2497px;width:405px;height:67px}
.f-phone{left:612px;top:2497px;width:406px;height:67px}
.f-email{left:184px;top:2593px;width:405px;height:67px}
.f-address{left:612px;top:2593px;width:406px;height:67px}
.f-message{left:184px;top:2688px;width:832px;height:110px}
.submit{left:514px;top:2839px;width:162px;height:61px;font-size:18px}
.submit::after{left:8px;top:8px}

/* footer */
.footer-brand{left:478px;top:3158px;width:245px;height:95px;display:flex;align-items:center;justify-content:center;
  font-size:54px;font-weight:300;letter-spacing:1px;color:var(--cream)}
.footer-nav{left:0;top:3297px;width:1200px;display:flex;justify-content:center;gap:39px;font-size:14.5px;list-style:none}
.footer-rule{left:114px;top:3350px;width:974px;height:2px;background:#bdbab3}
.copyright{left:0;top:3386px;width:1200px;text-align:center;font-size:16px}
</style>
</head>
<body>
<div class="page">

  <!-- backgrounds -->
  <div class="abs bg-footer"></div>
  <div class="abs bg-contact"></div>
  <div class="abs bg-services"></div>
  <div class="abs bg-navy"></div>

  <!-- hero -->
  <div class="abs hero-visual" role="img" aria-label="Glowing blue rising bar chart over a digital data grid"></div>
  <svg class="abs divider" style="top:640px" width="1200" height="160" viewBox="0 640 1200 160">
    <polygon fill="var(--cream)" points="0,783 847,667 1200,730 1200,761 847,697 0,790"/>
  </svg>

  <header class="abs site-header">
    <div class="abs brand">VELIM</div>
    <svg class="abs icon-search" width="28" height="28" viewBox="0 0 28 28" aria-label="Search">
      <circle cx="11" cy="11" r="8" fill="none" stroke="var(--white)" stroke-width="3.5"/>
      <line x1="17" y1="17" x2="25" y2="25" stroke="var(--white)" stroke-width="4" stroke-linecap="round"/>
    </svg>
    <svg class="abs icon-menu" width="34" height="28" viewBox="0 0 34 28" aria-label="Menu">
      <rect x="0" y="1" width="34" height="4" rx="1" fill="var(--white)"/>
      <rect x="0" y="12" width="34" height="4" rx="1" fill="var(--white)"/>
      <rect x="0" y="23" width="34" height="4" rx="1" fill="var(--white)"/>
    </svg>
  </header>

  <p class="abs hero-kicker">WELCOME TO</p>
  <h1 class="abs hero-title">VELIM</h1>
  <a class="btn-frame hero-cta">GET STARTED</a>

  <!-- about -->
  <section>
    <div class="abs frame about-frame-a"></div>
    <div class="abs frame about-frame-b"></div>
    <h2 class="abs about-title">ABOUT US</h2>
    <p class="abs about-text">Lorem ipsum dolor sit amet, consectetur adipiscing elit, sed do eiusmod tempor incididunt ut labore et dolore magna aliqua. Ut enim ad minim veniam, quis nostrud exercitation ullamco laboris nisi ut aliquip ex ea commodo consequat. Duis aute irure dolor in reprehenderit in voluptate velit esse cillum dolore eu fugiat nulla pariatur. Excepteur sint occaecat cupidatat non proident, sunt in culpa qui officia deserunt mollit anim id est laborum.</p>
  </section>

  <svg class="abs divider" style="top:1420px" width="1200" height="150" viewBox="0 1420 1200 150">
    <polygon fill="var(--navy-deep)" points="0,1420 1200,1420 1200,1432 354,1520 0,1460"/>
    <polygon fill="var(--cream)" points="0,1460 354,1520 1200,1432 1200,1440 354,1556 0,1470"/>
  </svg>

  <!-- services -->
  <section>
    <h2 class="abs section-title services-title">OUR SERVICES</h2>
    <article class="abs service-card card-1">
      <div class="thumb thumb-ads" role="img" aria-label="Person working on a laptop showing a blog page"></div>
      <h3>Advertising</h3>
      <p style="top:270px">Lorem ipsum dolor sit amet, consectetur adipiscing elit, sed do eiusmod tempor</p>
    </article>
    <article class="abs service-card card-2">
      <div class="thumb thumb-data" role="img" aria-label="Hand pointing at analytics charts on a tablet"></div>
      <h3>Data analytics</h3>
      <p style="top:270px">Lorem ipsum dolor sit amet, consectetur adipiscing elit, sed do eiusmod tempor</p>
    </article>
    <article class="abs service-card card-3">
      <div class="thumb thumb-crm" role="img" aria-label="Hands holding a phone surrounded by glowing customer icons"></div>
      <h3>Customer relationship Management</h3>
      <p style="top:298px">Lorem ipsum dolor sit amet, consectetur adipiscing elit, sed do</p>
    </article>
  </section>

  <svg class="abs divider" style="top:2195px" width="1200" height="140" viewBox="0 2195 1200 140">
    <polygon fill="var(--cream)" points="0,2291 354,2202 1200,2311 1200,2325 354,2236 0,2300"/>
    <polygon fill="var(--charcoal)" points="0,2195 1200,2195 1200,2311 354,2202 0,2291"/>
  </svg>

  <!-- contact -->
  <section>
    <h2 class="abs section-title contact-title">CONTACT US</h2>
    <div class="field f-name">Name</div>
    <div class="field f-phone">Phone</div>
    <div class="field f-email">Email</div>
    <div class="field f-address">Address</div>
    <div class="field f-message">Message</div>
    <a class="btn-frame submit">SUBMIT</a>
  </section>

  <svg class="abs divider" style="top:2980px" width="1200" height="130" viewBox="0 2980 1200 130">
    <polygon fill="#172b39" points="0,2980 1200,2980 1200,3015 847,3068 0,2985"/>
    <polygon fill="var(--cream)" points="0,2985 847,3068 1200,3015 1200,3028 847,3106 0,2995"/>
  </svg>

  <!-- footer -->
  <footer>
    <div class="abs footer-brand">VELIM</div>
    <ul class="abs footer-nav">
      <li>Home</li><li>About Us</li><li>Services</li><li>Testimonials</li><li>Blog</li>
    </ul>
    <div class="abs footer-rule"></div>
    <p class="abs copyright">Copyright ©2023&nbsp; VELIM. All Rights Reserved.</p>
  </footer>
</div>
</body>
</html>
```